Mindfulness School for Children -- Business Cards

We're looking for business cards for our school directors and owners. We're a mindfulness school for children called little lanterns. Attached are our logos/icons.

```html
<!DOCTYPE html>
<html lang="en">
<head>
<meta charset="utf-8">
<title>little lanterns — Business Cards</title>
<link rel="stylesheet" href="https://fonts.googleapis.com/css2?family=Arimo:wght@400;700&display=swap">
<style>
  :root {
    --page-bg: #161616;
    --card-bg: #252525;
    --ink-white: #f2f2f2;
    --ink-soft: #d6d6d6;
    --teal: #5fb8cc;
    --mint: #8fd3a5;
    --divider: #6bbfae;
    --edge-start: #5fb3cf;
    --edge-mid: #9fdcb0;
    --edge-end: #7cc6d6;
    --pattern-dark: #1c1c1c;
    --pattern-light: #8a8a8a;
  }
  * { box-sizing: border-box; margin: 0; padding: 0; }
  html, body { width: 1200px; height: 900px; overflow: hidden; }
  body {
    background: var(--page-bg);
    font-family: "Arimo", Arial, sans-serif;
    display: flex;
    flex-direction: column;
    align-items: center;
    justify-content: center;
    gap: 56px;
  }
  .card {
    width: 600px;
    height: 343px;
    border-radius: 18px;
    overflow: hidden;
    position: relative;
  }
  .card-front {
    background: var(--card-bg);
    border-bottom: 6px solid transparent;
    background-image:
      linear-gradient(var(--card-bg), var(--card-bg)),
      linear-gradient(90deg, var(--edge-start), var(--edge-mid) 70%, var(--edge-end));
    background-origin: border-box;
    background-clip: padding-box, border-box;
  }
  .brand {
    position: absolute;
    top: 62px;
    left: 0;
    right: 0;
    display: flex;
    justify-content: center;
    align-items: center;
    gap: 14px;
  }
  .brand-name {
    font-size: 50px;
    font-weight: 700;
    color: var(--mint);
    letter-spacing: 0.5px;
  }
  .brand-dot {
    width: 16px;
    height: 16px;
    border-radius: 50%;
    background: var(--teal);
  }
  .details {
    position: absolute;
    top: 176px;
    left: 48px;
    right: 40px;
    display: flex;
    align-items: stretch;
  }
  .person { width: 250px; text-align: right; padding-right: 22px; }
  .person-name {
    font-size: 24px;
    font-weight: 700;
    color: var(--teal);
    letter-spacing: 0.5px;
  }
  .person-role {
    font-size: 14px;
    color: var(--ink-soft);
    margin-top: 6px;
  }
  .divider { width: 1px; background: var(--divider); }
  .contact {
    list-style: none;
    padding-left: 20px;
    font-size: 14.5px;
    color: var(--ink-white);
    display: flex;
    flex-direction: column;
    gap: 6px;
  }
  .contact li { display: flex; align-items: center; gap: 8px; }
  .contact svg { width: 12px; height: 12px; flex: none; fill: var(--teal); }
  .address {
    position: absolute;
    left: 48px;
    bottom: 34px;
    font-size: 14.5px;
    color: var(--ink-white);
  }
  .card-back { background: var(--pattern-dark); }
  .back-pattern {
    position: absolute;
    inset: 0;
    background: linear-gradient(125deg, var(--pattern-dark) 0%, #2a2a2a 50%, var(--pattern-light) 100%);
  }
</style>
</head>
<body>
  <section class="card card-front" aria-label="Business card front">
    <div class="brand">
      <span class="brand-name">little lanterns</span>
      <span class="brand-dot"></span>
    </div>
    <div class="details">
      <div class="person">
        <p class="person-name">NORA WHITFIELD</p>
        <p class="person-role">CEO/Founder</p>
      </div>
      <div class="divider"></div>
      <ul class="contact">
        <li><svg viewBox="0 0 24 24"><path d="M6.6 10.8a15 15 0 0 0 6.6 6.6l2.2-2.2a1 1 0 0 1 1-.25 11.4 11.4 0 0 0 3.6.57 1 1 0 0 1 1 1V20a1 1 0 0 1-1 1A17 17 0 0 1 3 4a1 1 0 0 1 1-1h3.5a1 1 0 0 1 1 1c0 1.25.2 2.45.57 3.57a1 1 0 0 1-.25 1z"/></svg>(00) 3920 6614</li>
        <li><svg viewBox="0 0 24 24"><path d="M7 1h10a2 2 0 0 1 2 2v18a2 2 0 0 1-2 2H7a2 2 0 0 1-2-2V3a2 2 0 0 1 2-2zm0 3v14h10V4zm5 15.5a1 1 0 1 0 0 2 1 1 0 0 0 0-2z"/></svg>(00) 7281 4053</li>
        <li><svg viewBox="0 0 24 24"><path d="M2 5h20v14H2zm2 2v.5l8 5 8-5V7zm0 2.8V17h16V9.8l-8 5z"/></svg>hello@littlelanterns.com</li>
        <li><svg viewBox="0 0 24 24"><path d="M12 2a10 10 0 1 0 0 20 10 10 0 0 0 0-20zm0 2a8 8 0 0 1 7.7 6H15a12 12 0 0 0-2-5.9A8 8 0 0 1 12 4zM4.3 14h4.3a12 12 0 0 0 2 5.9A8 8 0 0 1 4.3 14zm0-4A8 8 0 0 1 10.6 4.1 12 12 0 0 0 8.6 10zm6.3 0a10 10 0 0 1 1.4-4.6 10 10 0 0 1 1.4 4.6zm0 4h2.8a10 10 0 0 1-1.4 4.6 10 10 0 0 1-1.4-4.6zm2.8 5.9a12 12 0 0 0 2-5.9h4.3a8 8 0 0 1-6.3 5.9z"/></svg>www.littlelanterns.com</li>
      </ul>
    </div>
    <p class="address">Po Box 4120 Willow Lane Brookfield, AB 52318</p>
  </section>

  <section class="card card-back" aria-label="Business card back">
    <div class="back-pattern" role="img" aria-label="Repeating flower pattern in dark and silver tones across the card back"></div>
  </section>
</body>
</html>
```